Business Card for Polygraph business in Africa

Business Card . Polygraph Examiner based in Tanzania, East Africa.
Business Card will be used to disseminate contact information to potential clients.
It should convey that I am a professional specifically in the polygraph field and perform my work with integrity.

I have attached the business card that I'm currently using, which I threw together myself initially. It's not professional enough.

Target Market(s)

Banks, Accounting Firms, Government Ministries, Gas, Oil, & Gemstone Mining Concerns, Wildlife Conservation NGOs, International companies located in East Africa.

Industry/Entity Type

Business

Contact Information for Business Card

Veritrace Kilonga
Miriam Holloway
PO Box 48317
Arusha, Tanzania
+255 612 839 274
miriamholloway@postvale.example

Colors
00a990
f37122
faa54b

Requirements
Must have
• - Veritrace Kilonga (with the word "Polygraph" being more prominent than the word "Tanzania")
• - Forensic Examinations
• - Employment Screening
• - Should contain a logo of the Continental Truthline Society (of which I'm a member)
• - I would like an accent design (such as the polygraph "squiggles" of a cardio tracing or such as that)
• - My contact information (less prominent, but large enough to read legibly). I would also consider putting the contact information on the second side of the card.
Nice to have
• My color suggestions are changeable.
Should not have
• Anything "cutesy" or "cartoonish"

```html
<!DOCTYPE html>
<html lang="en">
<head>
<meta charset="utf-8">
<title>Veritrace Kilonga – Business Card</title>
<link rel="stylesheet" href="https://fonts.googleapis.com/css2?family=Open+Sans:wght@400;600&display=swap">
<style>
  :root {
    --stage: #3a3a3a;
    --card: #1b1b1b;
    --card-edge: #262626;
    --ink-grey: #a9a9a9;
    --ink-light: #e6e6e6;
    --teal: #00a990;
    --orange: #f37122;
    --badge: #d8d8d8;
  }
  * { margin: 0; padding: 0; box-sizing: border-box; }
  html, body { width: 1200px; height: 900px; overflow: hidden; }
  body {
    background: var(--stage);
    font-family: "Open Sans", Arial, sans-serif;
    display: flex;
    flex-direction: column;
    align-items: center;
    justify-content: center;
    gap: 56px;
  }
  .card {
    position: relative;
    width: 588px;
    height: 336px;
    background: var(--card);
    border: 1px solid var(--card-edge);
    border-radius: 18px;
    box-shadow: 0 14px 30px rgba(0,0,0,.45);
  }

  /* Front */
  .front .member-badge {
    position: absolute;
    top: 26px;
    right: 30px;
    width: 64px;
    height: 64px;
    border-radius: 50%;
    background: var(--badge);
  }
  .front .brand-name {
    position: absolute;
    top: 118px;
    left: 0;
    right: 0;
    text-align: center;
    font-size: 46px;
    font-weight: 400;
    color: var(--ink-grey);
    letter-spacing: .5px;
  }
  .front .services {
    position: absolute;
    bottom: 58px;
    left: 0;
    right: 0;
    text-align: center;
    font-size: 15px;
    color: var(--ink-light);
    letter-spacing: .3px;
  }
  .front .services .divider { margin: 0 16px; }

  /* Back */
  .back .brand-name {
    position: absolute;
    left: 42px;
    top: 146px;
    font-size: 30px;
    font-weight: 400;
    color: var(--ink-grey);
  }
  .back .rule {
    position: absolute;
    left: 302px;
    top: 70px;
    width: 2px;
    height: 196px;
    background: var(--orange);
  }
  .back .contact {
    position: absolute;
    left: 326px;
    top: 80px;
    color: var(--teal);
    font-size: 13.5px;
    line-height: 1.35;
  }
  .back .person {
    font-size: 21px;
    color: var(--ink-grey);
    margin-bottom: 16px;
  }
  .back .line {
    display: flex;
    align-items: flex-start;
    gap: 10px;
    margin-bottom: 10px;
  }
  .back .line svg { flex: none; margin-top: 2px; fill: var(--teal); }
</style>
</head>
<body>

  <section class="card front">
    <div class="member-badge" role="img" aria-label="Membership badge of the Continental Truthline Society"></div>
    <div class="brand-name">Veritrace Kilonga</div>
    <p class="services">Issue investigation<span class="divider">|</span>Employment screening</p>
  </section>

  <section class="card back">
    <div class="brand-name">Veritrace Kilonga</div>
    <div class="rule"></div>
    <div class="contact">
      <p class="person">Miriam Holloway</p>
      <div class="line">
        <svg width="12" height="16" viewBox="0 0 12 16" aria-hidden="true"><path d="M6 0a6 6 0 0 0-6 6c0 4.5 6 10 6 10s6-5.5 6-10a6 6 0 0 0-6-6zm0 8.3A2.3 2.3 0 1 1 6 3.7a2.3 2.3 0 0 1 0 4.6z"/></svg>
        <span>PO Box 48317<br>Arusha, Tanzania</span>
      </div>
      <div class="line">
        <svg width="16" height="14" viewBox="0 0 16 14" aria-hidden="true"><path d="M1 4c0-2 3-3 7-3s7 1 7 3v1h-4V3.6C10 3.2 6 3.2 5 3.6V5H1zM3 6h10l2 7H1zm5 1.8a2 2 0 1 0 0 4 2 2 0 0 0 0-4z"/></svg>
        <span>+255 612 839 274</span>
      </div>
      <div class="line">
        <svg width="16" height="12" viewBox="0 0 16 12" aria-hidden="true"><path d="M0 0h16v1.2L8 6.5 0 1.2zM0 2.8l8 5.3 8-5.3V12H0z"/></svg>
        <span>miriamholloway@postvale.example</span>
      </div>
    </div>
  </section>

</body>
</html>
```